Laser Tattoo Removal Business Cards

We are looking for a professional business card design for a laser tattoo removal business. Ideally looking for a black business card design. The name of the business is Brightline Tattoo Removal. We place our cards at local tattoo shops so we ideally are looking for something trendy/edgy to draw both male and female clientele in.

Target Market(s)

Male/Female ages 18-60

Contact Information for Business Card

black background ideally.. hoping to stay within greys, whites and black

Font styles to use
Serif
Sans Serif

Colors
121212
a9a9a9
5c5c5c
f5f5f5
ffffff
7f7f7f
606060
848484
9d9d9d

Requirements
Must have
• Employee Info:
• Melissa Thornbury
• Chief Executive Offer
• m: 919.537.2846
• w: 919.362.4178
• f: 919.685.3907
• mthornbury@brightlinetattooremoval.example
• Address:
• 4615 Oakmere Pkwy, Suite 210
• Raleigh, NC 27654
• Website:
• www.brightlinetattooremoval.example
Nice to have
• Myabe business name on back or logo on back and employee info on the front

```html
<!DOCTYPE html>
<html lang="en">
<head>
<meta charset="utf-8">
<title>Brightline Tattoo Removal — Business Cards</title>
<link href="https://fonts.googleapis.com/css2?family=Oswald:wght@400&family=Roboto+Condensed:wght@400&family=Arimo:wght@400;700&display=swap" rel="stylesheet">
<style>
  :root {
    --ink: #121212;
    --charcoal: #1c1c1c;
    --grey-dark: #5c5c5c;
    --grey-mid: #7f7f7f;
    --grey-soft: #a9a9a9;
    --paper: #ffffff;
    --paper-tint: #f5f5f5;
    --backdrop: #d6d6d6;
  }
  * { margin: 0; padding: 0; box-sizing: border-box; }
  html, body { width: 1200px; height: 960px; overflow: hidden; }
  body {
    position: relative;
    background: var(--backdrop);
    font-family: "Arimo", Arial, sans-serif;
    color: var(--ink);
  }

  .card { position: absolute; width: 600px; height: 343px; overflow: hidden; }
  .card-front { left: 302px; top: 122px; }
  .card-back { left: 299px; top: 495px; }

  .card-texture { position: absolute; inset: 0; }
  .card-front .card-texture { background: radial-gradient(circle at 50% 50%, var(--paper) 0%, var(--paper-tint) 100%); }
  .card-back .card-texture { background: radial-gradient(circle at 50% 45%, #242424 0%, var(--ink) 100%); }

  .edge-tab { position: absolute; left: 0; top: 80px; width: 8px; height: 86px; background: var(--ink); }

  .front-brand {
    position: absolute; left: 66px; top: 98px; width: 140px;
    text-align: center;
    font-family: "Oswald", "Arial Narrow", sans-serif;
    font-size: 22px; line-height: 26px; letter-spacing: 1px;
    color: var(--ink);
  }

  .employee { position: absolute; left: 268px; top: 92px; }
  .employee-name {
    font-family: "Oswald", "Arial Narrow", sans-serif;
    font-size: 36px; line-height: 40px; letter-spacing: 0.5px;
    color: var(--ink); transform: scaleX(0.85); transform-origin: left;
  }
  .employee-title { font-size: 13.5px; color: var(--grey-mid); letter-spacing: 0.3px; line-height: 16px; }
  .employee-email {
    font-family: "Roboto Condensed", "Arial Narrow", sans-serif;
    font-size: 14px; color: var(--grey-mid); line-height: 18px;
  }

  .contact { position: absolute; left: 268px; top: 180px; display: flex; font-size: 13.5px; line-height: 18px; color: var(--ink); }
  .contact-phones { width: 127px; }
  .contact-divider { width: 1px; background: var(--grey-dark); margin-right: 16px; height: 50px; }

  .website {
    position: absolute; left: 268px; top: 251px;
    font-size: 13.5px; color: var(--grey-dark);
  }
  .website strong { font-weight: 700; }

  .back-brand {
    position: absolute; left: 0; right: 0; top: 122px;
    text-align: center;
    font-family: "Oswald", "Arial Narrow", sans-serif;
    font-size: 44px; line-height: 50px; letter-spacing: 3px;
    color: var(--paper-tint);
  }
</style>
</head>
<body>
  <section class="card card-front">
    <div class="card-texture" role="img" aria-label="Pale grey damask pattern across the card face"></div>
    <div class="edge-tab"></div>
    <div class="front-brand">BRIGHTLINE TATTOO REMOVAL</div>

    <div class="employee">
      <div class="employee-name">MELISSA THORNBURY</div>
      <div class="employee-title">CHIEF EXECUTIVE OFFER</div>
      <div class="employee-email">mthornbury@brightlinetattooremoval.example</div>
    </div>

    <div class="contact">
      <div class="contact-phones">
        919.537.2846 (m)<br>919.362.4178 (w)<br>919.685.3907 (f)
      </div>
      <div class="contact-divider"></div>
      <div class="contact-address">
        4615 Oakmere Pkwy<br>Suite 210<br>Raleigh, NC 27654
      </div>
    </div>

    <div class="website"><strong>BRIGHTLINETATTOOREMOVAL</strong>.example</div>
  </section>

  <section class="card card-back">
    <div class="card-texture" role="img" aria-label="Dark tone-on-tone damask pattern across the card back"></div>
    <div class="back-brand">BRIGHTLINE<br>TATTOO REMOVAL</div>
  </section>
</body>
</html>
```